design a construction company business card

Design business card around our logo. Card must have all the typical info: name, title, address, phone, email, business name, etc. Somewhere on the card I would like to see our motto "Built on integrity... Inspired by commitment." Consider adding a splash of bright orange to the card to complement the blues and silvers/grays in the logo. We are open to metallic inks, textures, etc. We would like to see options on both light and dark backgrounds. The font in the logo is Euro Technic Extended Regular.

```html
<!DOCTYPE html>
<html lang="en">
<head>
<meta charset="utf-8">
<title>Hollis Building, Inc. – Business Card</title>
<link rel="stylesheet" href="https://fonts.googleapis.com/css2?family=Source+Sans+3:wght@400;600;700&display=swap">
<style>
  :root {
    --stage-light: #e8e9eb;
    --stage-dark: #cfd0d2;
    --card-white: #ffffff;
    --card-black: #231f20;
    --band-start: #2a3d94;
    --band-end: #1f78c0;
    --rule-gray: #8a8c8f;
    --brand-blue: #2a4fa8;
    --icon-blue: #2770c4;
    --text-gray: #555759;
  }
  * { margin: 0; padding: 0; box-sizing: border-box; }
  html, body {
    width: 800px; height: 1200px; overflow: hidden;
  }
  body {
    position: relative;
    background: radial-gradient(ellipse at 50% 50%, var(--stage-light) 0%, var(--stage-dark) 80%);
    font-family: "Source Sans 3", sans-serif;
  }
  .card {
    position: absolute;
    left: 148px;
    width: 504px;
    height: 288px;
  }
  .card--front { top: 170px; background: var(--card-white); }
  .card--back { top: 703px; background: var(--card-black); }

  .rule {
    position: absolute; left: 0; right: 0; height: 2px;
    background: var(--rule-gray);
  }
  .rule--top { top: 17px; }
  .rule--bottom { top: 99px; }
  .name-band {
    position: absolute; left: 0; right: 0; top: 21px; height: 76px;
    background: linear-gradient(90deg, var(--band-start), var(--band-end));
    color: #fff; text-align: center;
  }
  .person-name {
    position: absolute; left: 0; right: 0; top: 14px;
    font-size: 24px; font-weight: 700; letter-spacing: 0.2px;
    padding-right: 20px;
  }
  .person-title {
    position: absolute; left: 0; right: 0; top: 46px;
    font-size: 13.5px; font-weight: 400;
  }

  .brand {
    position: absolute; display: flex; align-items: center; gap: 8px;
    font-weight: 600; white-space: nowrap;
  }
  .brand__mark { width: 15px; height: 15px; }
  .card--front .brand {
    left: 44px; top: 176px; font-size: 19px; color: var(--brand-blue);
  }
  .card--front .brand__mark { background: var(--brand-blue); }
  .card--back .brand {
    left: 0; right: 0; justify-content: center; top: 131px;
    font-size: 23px; color: #fff;
  }
  .card--back .brand__mark { background: #fff; }

  .divider {
    position: absolute; left: 241px; top: 162px; width: 1px; height: 64px;
    background: linear-gradient(180deg, transparent, #9a9c9f, transparent);
  }
  .contact {
    position: absolute; left: 253px; top: 134px;
    color: var(--text-gray); font-size: 13.5px; line-height: 17px;
  }
  .contact__address { margin-bottom: 13px; }
  .contact__list { list-style: none; }
  .contact__item {
    display: flex; align-items: center; gap: 6px; height: 18.5px;
  }
  .contact__icon { width: 9px; height: 9px; flex: none; }
</style>
</head>
<body>

<section class="card card--front">
  <div class="rule rule--top"></div>
  <header class="name-band">
    <div class="person-name">Daniel Whitford</div>
    <div class="person-title">Managing Member</div>
  </header>
  <div class="rule rule--bottom"></div>

  <div class="brand"><span class="brand__mark"></span>Hollis Building, Inc.</div>
  <div class="divider"></div>

  <div class="contact">
    <p class="contact__address">2287 Ridgeline Drive,<br>Folsom, CA 95630</p>
    <ul class="contact__list">
      <li class="contact__item">
        <svg class="contact__icon" viewBox="0 0 10 10"><path fill="var(--icon-blue)" d="M2 0.5 3.6 2.6 2.7 3.6C3.3 5 4.9 6.7 6.4 7.3L7.4 6.4 9.5 8 8.6 9.4C4.5 9.3 0.7 5.5 0.6 1.4Z"/></svg>
        (916) 555-0142
      </li>
      <li class="contact__item">
        <svg class="contact__icon" viewBox="0 0 10 10"><rect x="2.5" y="0.5" width="5" height="9" rx="1" fill="none" stroke="var(--icon-blue)" stroke-width="1.2"/><circle cx="5" cy="8" r="0.6" fill="var(--icon-blue)"/></svg>
        (530) 555-0187
      </li>
      <li class="contact__item">
        <svg class="contact__icon" viewBox="0 0 10 10"><rect x="0.5" y="2" width="9" height="6.5" fill="var(--icon-blue)"/><path d="M0.5 2 5 5.6 9.5 2" fill="none" stroke="#fff" stroke-width="0.9"/></svg>
        daniel@hollisbuild.com
      </li>
      <li class="contact__item">
        <svg class="contact__icon" viewBox="0 0 10 10"><g fill="none" stroke="var(--icon-blue)" stroke-width="0.9"><circle cx="5" cy="5" r="4.3"/><ellipse cx="5" cy="5" rx="1.8" ry="4.3"/><path d="M0.7 5H9.3M1.5 2.8H8.5M1.5 7.2H8.5"/></g></svg>
        www.hollisbuild.com
      </li>
    </ul>
  </div>
</section>

<section class="card card--back">
  <div class="brand"><span class="brand__mark"></span>Hollis Building, Inc.</div>
</section>

</body>
</html>
```